Redesign Canvas Art E-Commerce Website

Help! I hired a couple of companies on Brisklo.com to build and design an e-commerce website for me. After three long and painful months, I have one that I believe is functional on the back-end, but aesthetically on the front end is a mess.

We are a small family business that will take your digital photo and manipulate it into a digitally created oil, watercolor or impressionist style pieces of artwork that we print on museum quality, gallery grade canvas and ship to the customer, ready to hang.

We are looking to create an e-commerce website where a customer can choose their art style, upload a photo, choose their canvas size and orientation (horizontal or vertical) and checkout. Within 48 hours, we will send them back a proof of their newly created, customized artwork for them to approve or not approve. If they approve, we print, package and ship them the product. If they do not approve, we offer unlimited revisions until they are happy.

As I mentioned, the back end functionality is already there, just need design help. No coding required

Here is a link to the development page that they created: https://plumwickstudio.com/development/

As you can see, it looks off...doesnt line up properly, wasted space, weird font. Feel free to either correct the homepage they created or design an entirely new page. I am attaching some examples of before and after photos of artwork for reference. I also think the testimonials page and shop page can use a little style. The content is there and accurate, it just doesn't look pretty. Please keep in mind that our customers will probably not be very tech savvy. The customers will probably be sending us pics of kids, grandkids, pets, family portraits, vacation photos, etc.

Here is one of our competitors - www.gildavantry.com
Their website looks clean and inviting.

Thank you in advance! Im looking forward to seeing the results. I am including our logo in the attachments (I do not have it in a vector file, just a jpeg)

Target Market(s)

Non tech-savvy indiduals, 30-70 years old

Industry/Entity Type

Please look at https://plumwickstudio.com/development/ to see various pages and what the other designers did

Number of Pages Required

1 page

Requirements
Must have
• Verbiage on pages leave "as is" but feel free to change styles. Would like to keep existing four categories on homepage
Nice to have
• Warm and inviting homepage that evokes emotion

```html
<!DOCTYPE html>
<html lang="en">
<head>
<meta charset="utf-8">
<title>Plumwick Studio – Canvas Art</title>
<link rel="stylesheet" href="https://fonts.googleapis.com/css2?family=Montserrat:wght@400;500;600;700&family=Sacramento&display=swap">
<style>
:root{
  --ink:#111;
  --text:#333;
  --teal:#2aafcf;
  --red:#e8161f;
  --grey-bg:#f1f1f1;
  --hero-a:#d9d9d9;
  --hero-b:#b9bdb8;
  --white:#fff;
  --line:#dcdcdc;
}
*{margin:0;padding:0;box-sizing:border-box}
html,body{width:1200px;height:3604px;overflow:hidden;background:var(--white)}
body{position:relative;font-family:"Montserrat",sans-serif;color:var(--text)}
.abs{position:absolute}
.script{font-family:"Sacramento",cursive;color:var(--teal);font-size:34px;line-height:1}
.btn{position:absolute;display:flex;align-items:center;justify-content:center;color:var(--white);font-weight:700;font-size:15px;text-transform:uppercase;text-decoration:none}
.btn-teal{background:var(--teal);border-radius:10px 0 10px 0}
.btn-red{background:var(--red);border-radius:28px}
.brand{font-weight:700;color:var(--ink);display:flex;align-items:center;gap:8px;white-space:nowrap}
.brand .dot{width:20px;height:20px;border-radius:50%;background:var(--teal);flex:none}
.nav{position:absolute;top:38px;left:322px;font-size:15px;color:var(--ink)}
.nav a{position:absolute;white-space:nowrap;color:var(--ink);text-decoration:none}
.hero{left:0;top:102px;width:1200px;height:600px;border-radius:80px;background:linear-gradient(120deg,var(--hero-a),var(--hero-b) 60%,#c9cbc7)}
.photo{position:absolute;border:8px solid var(--white);border-radius:12px;box-shadow:0 6px 18px rgba(0,0,0,.2)}
.about p{font-size:16px;line-height:30px;color:var(--text)}
h2.title{font-weight:700;color:var(--ink);text-transform:uppercase}
.cat{position:absolute;top:1547px;width:226px;height:293px;border:9px solid var(--ink);border-radius:26px;background:var(--white);padding:8px}
.cat .pic{height:180px;border-radius:10px 10px 0 0}
.cat .label{background:#ededed;height:82px;border-radius:0 0 12px 12px;text-align:center;padding-top:16px}
.cat small{display:block;font-size:10px;font-weight:600;color:var(--ink)}
.cat strong{display:block;font-size:18px;font-weight:600;color:var(--ink);margin-top:8px}
.why{position:absolute;top:2632px;width:263px;height:298px;background:var(--white);border-radius:14px;box-shadow:0 4px 24px rgba(0,0,0,.08);padding:22px 26px}
.why .icon{width:66px;height:66px;border-radius:50%;background:var(--teal);display:flex;align-items:center;justify-content:center}
.why h3{font-size:21px;font-weight:700;color:var(--ink);margin:24px 0 14px;line-height:24px}
.why p{font-size:13px;line-height:26px;color:var(--text)}
.foot h4{font-size:22px;font-weight:500;color:var(--ink);margin-bottom:14px}
.foot li{list-style:none;font-size:14px;line-height:32px;color:var(--text);display:flex;align-items:center;gap:6px}
.social{display:flex;gap:10px}
.social span{width:26px;height:26px;border-radius:50%;background:#e4e4e4}
.social span.on{background:var(--red)}
.rule{left:112px;width:978px;height:1px;background:var(--line)}
</style>
</head>
<body>

<header>
  <div class="abs brand" style="left:112px;top:34px;font-size:17px"><span class="dot"></span>Plumwick Studio</div>
  <nav class="nav">
    <a style="left:0">Home</a><a style="left:74px">Shop</a><a style="left:142px">Testimonials</a>
    <a style="left:263px">About Us</a><a style="left:359px">FAQs</a><a style="left:428px">My Orders</a><a style="left:531px">Contact Us</a>
  </nav>
  <a class="btn btn-teal" style="left:964px;top:22px;width:123px;height:44px">
    <svg width="13" height="13" viewBox="0 0 12 12" style="margin-right:6px"><circle cx="6" cy="3.5" r="3" fill="#fff"/><path d="M0 12c0-4 3-5.5 6-5.5s6 1.5 6 5.5z" fill="#fff"/></svg>Login</a>
</header>

<section class="abs hero" role="img" aria-label="Soft blurred background photo of a family moment with flowers"></section>
<div class="abs" style="left:112px;top:244px;font-size:44px;color:var(--ink)">Welcome To</div>
<div class="abs brand" style="left:112px;top:338px;font-size:36px;gap:10px"><span class="dot" style="width:40px;height:40px"></span>Plumwick Studio</div>
<a class="btn btn-teal" style="left:112px;top:470px;width:157px;height:50px">Get Started</a>
<div class="photo" role="img" aria-label="Puppy portrait painted on canvas" style="left:592px;top:230px;width:200px;height:300px;transform:rotate(-8deg);background:linear-gradient(150deg,#6b5a4a,#c9c2b8 60%,#8a7d6e)"></div>
<div class="photo" role="img" aria-label="Father and child walking, painted on canvas" style="left:870px;top:230px;width:200px;height:300px;transform:rotate(8deg);background:linear-gradient(160deg,#8aa06a,#d7b56a 40%,#5a7aa0)"></div>
<div class="photo" role="img" aria-label="Bride holding bouquet, painted on canvas" style="left:718px;top:294px;width:228px;height:302px;background:linear-gradient(150deg,#3a2a20,#b07a52 45%,#c8d27a 80%)"></div>

<section class="about">
  <div class="abs" role="img" aria-label="Puppy photo framed in a paint splash shape" style="left:112px;top:770px;width:434px;height:505px;border-radius:48% 52% 44% 56%/40% 46% 54% 60%;background:radial-gradient(circle at 50% 45%,#f2eee8,#8c8178 55%,#5a6f78 90%,transparent 92%)"></div>
  <div class="abs script" style="left:582px;top:784px">About Us</div>
  <h2 class="abs title" style="left:580px;top:822px;font-size:40px">Plumwick Studio</h2>
  <div class="abs" style="left:580px;top:880px;width:520px">
    <p>At Plumwick Studio, we take your digital photo and turn it into a one-of-a-kind piece of artwork!</p>
    <p style="margin-top:30px">The process couldn't be any easier. Simply upload your photo, choose your art style and size, and let our team of skilled digital artists do the rest. Do you want to put your digital photo on canvas without an art style? No problem! Just choose the “Digital Photo/Retouching” category and upload your photo. We can print your photo “as is” or do some minor retouching (e.g. remove objects, enhance colors, lighten photo, etc)</p>
  </div>
  <a class="btn btn-teal" style="left:580px;top:1203px;width:157px;height:51px">Learn More</a>
</section>

<section class="abs" style="left:0;top:1350px;width:1200px;height:578px;background:var(--grey-bg)"></section>
<div class="abs script" style="left:0;width:1200px;text-align:center;top:1436px;font-size:28px">Shop Now</div>
<h2 class="abs title" style="left:0;width:1200px;text-align:center;top:1466px;font-size:34px">Categories</h2>
<div class="cat" style="left:115px"><div class="pic" role="img" aria-label="Couple wedding portrait" style="background:linear-gradient(150deg,#3e5a2e,#c9c0b0 60%,#6a4a32)"></div><div class="label"><small>MOST POPULAR</small><strong>OIL</strong></div></div>
<div class="cat" style="left:362px"><div class="pic" role="img" aria-label="Mother and baby portrait" style="background:linear-gradient(150deg,#f4e6dc,#e8c4ae 60%,#fbf4ee)"></div><div class="label"><small>MOST POPULAR</small><strong>WATERCOLOR</strong></div></div>
<div class="cat" style="left:611px"><div class="pic" role="img" aria-label="Grandparents laughing together" style="background:linear-gradient(150deg,#5f8a4a,#a8c0cc 55%,#4f7fa8)"></div><div class="label"><small>MOST POPULAR</small><strong>IMPRESSIONIST</strong></div></div>
<div class="cat" style="left:859px"><div class="pic" role="img" aria-label="Father and child walking on a path" style="background:linear-gradient(160deg,#4d6a3a,#a69a82 55%,#6a7a8e)"></div><div class="label"><small>MOST POPULAR</small><strong>DIGITAL PHOTO</strong></div></div>

<section class="abs" style="left:0;top:1927px;width:1200px;height:518px;background:var(--teal)"></section>
<div class="abs" role="img" aria-label="Dog and cat resting together, painted on canvas" style="left:155px;top:1987px;width:359px;height:317px;border:6px solid var(--white);background:linear-gradient(140deg,#f0ede8,#b0662e 45%,#3a2518 70%,#e8e4dc)"></div>
<div class="abs" role="img" aria-label="Dog and cat thumbnail" style="left:155px;top:2322px;width:86px;height:64px;border:2px solid var(--white);background:linear-gradient(140deg,#e8e2d8,#a8602c)"></div>
<div class="abs" role="img" aria-label="Mother and baby thumbnail" style="left:244px;top:2322px;width:86px;height:64px;border:2px solid var(--white);background:linear-gradient(140deg,#f4e6dc,#d8b09a)"></div>
<div class="abs" role="img" aria-label="Grandparents thumbnail" style="left:334px;top:2322px;width:86px;height:64px;border:2px solid var(--white);background:linear-gradient(140deg,#6a9050,#8fb0c4)"></div>
<div class="abs" role="img" aria-label="Puppy thumbnail" style="left:424px;top:2322px;width:86px;height:64px;border:2px solid var(--white);background:linear-gradient(140deg,#6b5a4a,#c8c0b6)"></div>
<div class="abs script" style="left:574px;top:2008px;color:var(--red)">Canvas Art</div>
<h2 class="abs title" style="left:574px;top:2046px;width:560px;font-size:42px;line-height:51px;color:var(--white)">From Photo to Museum Quality Canvas Art</h2>
<p class="abs" style="left:574px;top:2216px;width:480px;font-size:15px;line-height:30px;color:var(--white)">Lorem ipsum dolor sit amet, consectetur adipiscing elit, sed do eiusmod tempor incididunt ut labore et dolore magna aliqua.</p>
<a class="btn btn-red" style="left:570px;top:2295px;width:165px;height:56px">Learn More</a>

<div class="abs script" style="left:0;width:1200px;text-align:center;top:2516px">My Orders</div>
<h2 class="abs title" style="left:0;width:1200px;text-align:center;top:2548px;font-size:34px">Why Us?</h2>
<div class="why" style="left:160px"><div class="icon"><svg width="34" height="34" viewBox="0 0 24 24" fill="none" stroke="#fff" stroke-width="1.5"><path d="M12 3a6 6 0 0 0-3.5 10.9V17h7v-3.1A6 6 0 0 0 12 3z"/><path d="M9.5 20h5M10 13l2-3 2 3"/></svg></div><h3>Your Idea Your Design</h3><p>Each art piece is customized for you! You choose your size, orientation and art style. Makes a perfect gift!!!</p></div>
<div class="why" style="left:469px"><div class="icon"><svg width="34" height="34" viewBox="0 0 24 24" fill="none" stroke="#fff" stroke-width="1.5"><rect x="3" y="7" width="11" height="9"/><path d="M14 10h4l3 3v3h-7"/><circle cx="7" cy="17.5" r="1.5"/><circle cx="17" cy="17.5" r="1.5"/></svg></div><h3>Fast Shipping</h3><p>Your artwork is printed and shipped in the USA! We offer fast turnaround with transit times typically 3-7 days. Free tracking with each order!!</p></div>
<div class="why" style="left:777px"><div class="icon"><svg width="34" height="34" viewBox="0 0 24 24" fill="none" stroke="#fff" stroke-width="1.5"><circle cx="12" cy="9" r="6"/><path d="M12 6l1 2 2 .3-1.5 1.4.4 2.1L12 10.8l-1.9 1 .4-2.1L9 8.3 11 8z"/><path d="M8.5 14l-1.5 7 5-2 5 2-1.5-7"/></svg></div><h3>High Quality</h3><p>We've put a lot of effort ensuring your artwork is of the highest quality. Each piece is printed on the highest quality, gallery grade canvas. It is ready to hang upon arrival.!</p></div>

<div class="abs script" style="left:0;width:1200px;text-align:center;top:2990px">Our Newsletter</div>
<h2 class="abs title" style="left:0;width:1200px;text-align:center;top:3036px;font-size:36px">Stay Informed With Our Latest News</h2>
<div class="abs" style="left:238px;top:3122px;width:540px;height:54px;border-radius:27px;background:#ebebeb;padding-left:32px;display:flex;align-items:center;font-size:16px;color:var(--text)">Enter Your Email</div>
<a class="btn btn-red" style="left:795px;top:3122px;width:180px;height:54px;text-transform:none;font-size:18px;font-weight:600">Subscribe</a>

<div class="abs rule" style="top:3237px"></div>
<footer class="foot">
  <div class="abs brand" style="left:112px;top:3336px;font-size:20px"><span class="dot" style="width:26px;height:26px"></span>Plumwick Studio</div>
  <div class="abs" style="left:416px;top:3292px"><h4>Contact Info</h4><ul>
    <li><svg width="12" height="14" viewBox="0 0 12 14"><path d="M6 0a5 5 0 0 0-5 5c0 4 5 9 5 9s5-5 5-9a5 5 0 0 0-5-5z" fill="#e8161f"/><circle cx="6" cy="5" r="2" fill="#fff"/></svg>12b Plumwick Studio omnis</li>
    <li><svg width="12" height="12" viewBox="0 0 12 12"><path d="M2 0l3 3-1.5 1.5a8 8 0 0 0 4 4L9 7l3 3-2 2C5 12 0 7 0 2z" fill="#e8161f"/></svg>+1 888 888 8888</li>
    <li><svg width="13" height="10" viewBox="0 0 13 10" fill="none" stroke="#e8161f"><rect x=".5" y=".5" width="12" height="9"/><path d="M.5 .5l6 5 6-5"/></svg>info@plumwickstudio.com</li></ul></div>
  <div class="abs" style="left:695px;top:3292px"><h4>Customer Service</h4><ul>
    <li>Terms &amp; conditions</li><li>Privacy Policy</li><li>About Us</li><li>FAQs</li></ul></div>
  <div class="abs" style="left:953px;top:3292px"><h4>Follow Us</h4>
    <div class="social"><span class="on" aria-label="Social page 1"></span><span aria-label="Social page 2"></span><span aria-label="Social page 3"></span><span aria-label="Social page 4"></span></div></div>
</footer>
<div class="abs rule" style="top:3495px"></div>
<p class="abs" style="left:0;width:1200px;text-align:center;top:3536px;font-size:14px;color:var(--ink)">©Copyrights 2023 <span style="color:var(--teal);text-decoration:underline">Plumwick Studio</span> &nbsp;| &nbsp;&nbsp;All Rights Reserved</p>

</body>
</html>
```